Child Sponsorship Charity Needs a Wordpress Design

BrightWell GLOBAL is a not-for-profit organization that breaks the cycle of poverty through child sponsorship. We work in 7 countries around the world and are based in Canada. We currently have a Wordpress website and want to update the look and create a more engaging user experience. Our donor base is across Canada and our partners work across the globe. PLEASE SEE THE DESIGN BRIEF ATTACHED. We are looking for out site to be clean, colourful, and inviting. It should maintain our brand image, be welcoming to potential donors, and a great resource to current donors.

Project Deadline Extended Reason: Our Board of Directors wants a chance to provide feedback on the submissions and so we are extending the deadline to give them the opportunity to share their insights. Added Saturday, February 21, 2015

Charity

• Helvetica / Helvetica Neue

• Got a list of colours from the designer who made our logo:
• Brightwell Navy blue
• C: 100
• M: 80
• Y: 0
• K: 23
• Or
• R: 2
• G: 60
• B: 132
• Brightwell lighter blue
• C: 34
• M: 0
• Y: 3
• K: 0
• Or
• R: 161
• G: 221
• B: 241
• Brightwell deep red (newsletter accent colour)
• C: 0
• M: 91
• Y: 88
• K: 30
• Or
• R: 178
• G: 44
• B: 34

```html
<!DOCTYPE html>
<html lang="en">
<head>
<meta charset="utf-8">
<title>BrightWell Global – Child Sponsorship</title>
<link href="https://fonts.googleapis.com/css2?family=Roboto:wght@400;500;700&family=Roboto+Slab:wght@700&family=Open+Sans:wght@400;700&display=swap" rel="stylesheet">
<style>
  :root{
    --blue:#1f8fd0;
    --blue-nav:#2a9ad8;
    --blue-band:#1b6db3;
    --blue-band-dark:#165b98;
    --grey-band:#3e3e3e;
    --grey-band-dark:#303030;
    --ink:#222;
    --text:#555;
    --footer-blue:#1e8fcf;
    --footer-dark:#2b2b2b;
    --white:#fff;
    --line:#c9c9c9;
  }
  *{margin:0;padding:0;box-sizing:border-box}
  html,body{width:770px;height:1200px;overflow:hidden;background:#fff}
  body{position:relative;font-family:'Roboto',Helvetica,Arial,sans-serif;color:var(--ink)}
  .abs{position:absolute}

  /* header */
  .phone{left:60px;top:34px;display:flex;align-items:center;gap:6px;font-size:16px;font-weight:500}
  .address{left:64px;top:58px;font-size:7px;color:#333}
  .brand{left:284px;top:30px;width:200px;display:flex;align-items:center;justify-content:center;gap:7px;font-size:15px;color:var(--blue-band-dark)}
  .brand .dot{width:14px;height:14px;border-radius:50%;background:var(--blue)}
  .btn-sponsor{left:594px;top:25px;width:118px;height:23px;background:#53aee3;color:#fff;font-size:10px;display:flex;align-items:center;justify-content:center;gap:6px}
  .btn-sponsor .dot{width:14px;height:14px;border-radius:50%;border:1.5px solid #fff}
  .search{left:594px;top:56px;width:118px;height:21px;border:1px solid #ccc;font-size:8px;color:#888;padding:6px 6px}
  .search .go{position:absolute;right:-1px;top:-1px;width:20px;height:21px;background:var(--blue);display:flex;align-items:center;justify-content:center}

  /* hero */
  .hero{left:0;top:117px;width:770px;height:329px;background:radial-gradient(ellipse at 55% 55%,#b9826a 0%,#a48f78 30%,#9a9886 60%,#b6b8ae 100%)}
  .hero-title{left:86px;top:238px;font-family:'Roboto Slab',Georgia,serif;font-size:24px;line-height:36px;color:#fff;text-shadow:0 1px 3px rgba(0,0,0,.45)}
  .arrow{top:250px}

  /* nav */
  .nav{left:60px;top:97px;width:652px;height:39px;background:linear-gradient(#36a4e0,#2088c9);display:flex;align-items:center;font-size:9.5px;color:#fff;box-shadow:0 3px 5px rgba(0,0,0,.2)}
  .nav a{color:#fff;text-decoration:none;padding:0 17.5px;height:39px;display:flex;align-items:center}
  .nav a.active{background:#111;padding:0 15px}

  /* band */
  .band{top:446px;height:87px}
  .band-blue{left:0;width:386px;background:var(--blue-band)}
  .band-grey{left:386px;width:384px;background:var(--grey-band)}
  .band-icon{top:446px;height:87px;display:flex;align-items:center;justify-content:center}
  .band-text{top:465px;color:#fff}
  .band-text h3{font-family:'Open Sans',Arial,sans-serif;font-size:13px;font-weight:700;margin-bottom:5px}
  .band-text p{font-family:'Open Sans',Arial,sans-serif;font-size:8.5px;line-height:16px}

  /* welcome */
  .welcome h2{font-size:14.5px;font-weight:400}
  .welcome h2 span{color:var(--blue)}
  .welcome p{font-size:9.6px;line-height:15.8px;color:var(--text);text-align:justify;width:336px;margin-top:8px}
  .btn{background:var(--blue);color:#fff;display:flex;align-items:center;justify-content:center;border-radius:2px;font-weight:500}
  .video-frame{left:410px;top:551px;width:302px;height:184px;border:1px solid #ccc;background:#fff;box-shadow:0 0 2px rgba(0,0,0,.1)}
  .video{left:417px;top:558px;width:287px;height:170px;background:linear-gradient(135deg,#6b5338,#4a3a2a 45%,#8a7560)}
  .video-bar{left:417px;top:706px;width:287px;height:22px;background:#1a1a1a;display:flex;align-items:center;gap:6px;padding:0 8px;color:#ddd;font-size:6px}
  .video-bar .track{flex:1;height:2px;background:#555;position:relative}
  .video-bar .track i{position:absolute;left:0;top:0;height:2px;width:35%;background:#e0393e}

  /* blog */
  .blog-head{left:58px;top:771px;font-size:12px;font-weight:500}
  .blog-head span{color:var(--blue)}
  .blog-rule{left:140px;top:778px;width:300px;height:1px;background:#888}
  .blog-nav{top:766px;width:14px;height:14px;background:#111;display:flex;align-items:center;justify-content:center}
  .thumb{top:799px;height:87px;border:3px solid #fff;box-shadow:0 0 2px rgba(0,0,0,.35)}
  .card-title{top:897px;font-size:7.2px;color:var(--blue)}
  .card-text{top:911px;width:136px;font-size:6.8px;line-height:10.5px;color:#666}
  .card-btn{top:937px;width:58px;height:19px;font-size:7px}
  .sponsor-img{left:495px;top:772px;width:215px;height:117px;border:3px solid #eee;box-shadow:0 0 2px rgba(0,0,0,.35);background:linear-gradient(120deg,#8f8a80,#5e5a55 55%,#a3a096)}
  .sponsor-img span{position:absolute;left:0;right:0;top:68px;text-align:center;color:#fff;font-size:15px;font-weight:700;text-shadow:0 1px 3px rgba(0,0,0,.5)}
  .donate-head{left:498px;top:898px;font-size:13.5px}
  .donate-head span{color:var(--blue)}
  .donate-text{left:498px;top:920px;font-size:6.8px;color:#777;width:215px;white-space:nowrap;overflow:hidden}

  /* footer */
  .footer{left:0;top:986px;width:770px;height:143px;background:var(--footer-blue);color:#fff}
  .f-col{top:1009px;font-size:8px;line-height:14.5px}
  .f-col h4{font-size:10px;font-weight:700;margin-bottom:7px;line-height:12px}
  .f-divider{top:1006px;width:1px;height:96px;background:rgba(255,255,255,.35)}
  .email{left:522px;top:1068px;width:148px;height:23px;background:#fff;color:#888;font-size:7px;padding:7px 8px}
  .submit{left:670px;top:1068px;width:42px;height:23px;background:#111;color:#fff;font-size:7.5px;font-weight:700;display:flex;align-items:center;justify-content:center}
  .bottom{left:0;top:1129px;width:770px;height:71px;background:var(--footer-dark)}
  .legal{left:56px;top:1150px;font-size:8px;color:#fff}
  .copy{left:56px;top:1168px;font-size:8px;color:#fff}
  .social{left:589px;top:1156px;display:flex}
  .social i{width:21px;height:20px;display:block}
</style>
</head>
<body>

<!-- header -->
<div class="abs phone">
  <svg width="17" height="17" viewBox="0 0 20 20"><circle cx="10" cy="10" r="9" fill="none" stroke="#1f8fd0" stroke-width="1.6"/><path d="M6.5 5.5l2 0 1 2.5-1.2 1a6 6 0 0 0 2.7 2.7l1-1.2 2.5 1v2c0 .6-.5 1-1 1A8 8 0 0 1 5.5 6.5c0-.5.4-1 1-1z" fill="#1f8fd0"/></svg>
  800-555-0142
</div>
<div class="abs address">1840 Harbor View Rd. Suite 210</div>

<div class="abs brand"><span class="dot"></span>BrightWell GLOBAL</div>

<div class="abs btn-sponsor"><span class="dot"></span>Sponsor a Child</div>
<div class="abs search">Search
  <span class="go"><svg width="10" height="10" viewBox="0 0 12 12"><circle cx="5" cy="5" r="3.5" fill="none" stroke="#fff" stroke-width="1.5"/><path d="M7.5 7.5L11 11" stroke="#fff" stroke-width="1.6"/></svg></span>
</div>

<!-- hero -->
<div class="abs hero" role="img" aria-label="Photo of two smiling boys embracing in a village street"></div>
<div class="abs hero-title">BRIGHTWELL<br>INTERNATIONAL</div>
<svg class="abs arrow" style="left:22px" width="22" height="44" viewBox="0 0 22 44"><path d="M20 2L3 22l17 20" fill="none" stroke="#fff" stroke-width="1.5"/></svg>
<svg class="abs arrow" style="left:726px" width="22" height="44" viewBox="0 0 22 44"><path d="M2 2l17 20L2 42" fill="none" stroke="#fff" stroke-width="1.5"/></svg>

<nav class="abs nav">
  <a class="active">HOME</a><a>ABOUT US</a><a>PROGRAMS</a><a>WHERE WE WORK</a><a>GET INVOLVED</a><a>CONTACT</a><a>BLOG</a><a>DONATE</a>
</nav>

<!-- programs band -->
<div class="abs band band-blue"></div>
<div class="abs band band-grey"></div>
<div class="abs band-icon" style="left:57px;width:83px;background:var(--blue-band-dark)">
  <svg width="54" height="48" viewBox="0 0 54 48"><path d="M27 46C10 34 2 25 2 15 2 7 8 2 15 2c5 0 9 3 12 7 3-4 7-7 12-7 7 0 13 5 13 13 0 10-8 19-25 31z" fill="#fff"/><path d="M12 24l10-8 8 5M20 30l8-6M25 34l7-5M30 37l5-4" stroke="#165b98" stroke-width="2" fill="none" stroke-linecap="round"/></svg>
</div>
<div class="abs band-icon" style="left:386px;width:84px;background:var(--grey-band-dark)">
  <svg width="46" height="52" viewBox="0 0 46 52"><path d="M8 24l8 10V8a3 3 0 0 1 6 0v16V4a3 3 0 0 1 6 0v20V7a3 3 0 0 1 6 0v19l4-8a3 3 0 0 1 5 2l-7 17c-3 8-8 13-16 13-7 0-12-5-14-11L4 27a3 3 0 0 1 4-3z" fill="none" stroke="#fff" stroke-width="2.2" stroke-linejoin="round"/></svg>
</div>
<div class="abs band-text" style="left:164px">
  <h3>OUR PROGRAMS</h3>
  <p>SPONSORING A CHILD THROUGH BRIGHTWELL<br>INTERNATIONAL ENABLES US...</p>
</div>
<div class="abs band-text" style="left:491px">
  <h3>WHERE WE WORK</h3>
  <p>SPONSORING A CHILD THROUGH BRIGHTWELL<br>INTERNATIONAL ENABLES US...</p>
</div>

<!-- welcome -->
<section class="abs welcome" style="left:57px;top:566px">
  <h2>WELCOME TO <span>BRIGHTWELL INTERNATIONAL</span></h2>
  <p>&nbsp;Lorem Ipsum has been the industry's standard dummy text ever since the 1500s, when an unknown printer took a galley of type and scrambled it to make a type specimen book. It has survived not only five centuries, but also the leap into electronic typesetting, remaining essentially unchanged. It was popularised in the 1960s with the release of Letraset sheets containing Lorem Ipsum passages, and more recently with desktop publishing</p>
</section>
<div class="abs btn" style="left:57px;top:704px;width:78px;height:23px;font-size:9px">READ MORE</div>

<div class="abs video-frame"></div>
<div class="abs video" role="img" aria-label="Video still of two young girls in white dresses at school"></div>
<svg class="abs" style="left:545px;top:608px" width="34" height="34" viewBox="0 0 34 34"><circle cx="17" cy="17" r="16" fill="rgba(0,0,0,.5)"/><path d="M13 10l11 7-11 7z" fill="#fff"/></svg>
<div class="abs video-bar">
  <svg width="11" height="11" viewBox="0 0 12 12"><circle cx="6" cy="6" r="5" fill="none" stroke="#fff" stroke-width="1.2"/><path d="M5 3.5l3 2.5-3 2.5z" fill="#fff"/></svg>
  <svg width="22" height="8" viewBox="0 0 22 8"><path d="M0 2h2l2-2v8l-2-2H0z" fill="#e0393e"/><path d="M8 1v6M10 1v6M12 1v6M14 1v6M16 1v6M18 1v6" stroke="#e0393e" stroke-width="1"/></svg>
  <span class="track"><i></i></span>
  <span>01:30 / 04:55</span>
  <svg width="9" height="7" viewBox="0 0 9 7"><rect x=".5" y=".5" width="8" height="6" fill="none" stroke="#fff"/></svg>
  <svg width="8" height="8" viewBox="0 0 8 8"><circle cx="4" cy="4" r="3" fill="none" stroke="#fff" stroke-width="1.6" stroke-dasharray="1.5 .8"/></svg>
</div>

<!-- latest blog -->
<div class="abs blog-head">LATEST <span>BLOG</span></div>
<div class="abs blog-rule"></div>
<div class="abs blog-nav" style="left:445px"><svg width="6" height="8" viewBox="0 0 6 8"><path d="M5 0L1 4l4 4" fill="none" stroke="#fff" stroke-width="1.3"/></svg></div>
<div class="abs blog-nav" style="left:460px"><svg width="6" height="8" viewBox="0 0 6 8"><path d="M1 0l4 4-4 4" fill="none" stroke="#fff" stroke-width="1.3"/></svg></div>

<div class="abs thumb" style="left:59px;width:134px;background:linear-gradient(135deg,#6d5a4a,#8fa3a0 60%,#c9c6b8)" role="img" aria-label="Photo of a smiling young girl in class"></div>
<div class="abs thumb" style="left:203px;width:132px;background:linear-gradient(135deg,#3c3a45,#2c4f86 55%,#c9c4bd)" role="img" aria-label="Photo of a schoolboy writing at his desk"></div>
<div class="abs thumb" style="left:346px;width:132px;background:linear-gradient(135deg,#a0622e,#6b4530 55%,#d8c6a6)" role="img" aria-label="Photo of a laughing schoolboy with classmates"></div>

<div class="abs card-title" style="left:60px">IPSUM IS SIMPLY DUMMY TEXT</div>
<div class="abs card-text" style="left:59px">Lorem Ipsum has been the industry's standard dummy text ever since</div>
<div class="abs btn card-btn" style="left:59px">READ MORE</div>

<div class="abs card-title" style="left:206px">IPSUM IS SIMPLY DUMMY TEXT</div>
<div class="abs card-text" style="left:205px">Lorem Ipsum has been the industry's standard dummy text ever since</div>
<div class="abs btn card-btn" style="left:205px">READ MORE</div>

<div class="abs card-title" style="left:348px">IPSUM IS SIMPLY DUMMY TEXT</div>
<div class="abs card-text" style="left:347px">Lorem Ipsum has been the industry's stan-dard dummy text ever since</div>
<div class="abs btn card-btn" style="left:347px">READ MORE</div>

<div class="abs sponsor-img" role="img" aria-label="Photo of children standing together outdoors"><span>Sponsor a Child</span></div>
<div class="abs donate-head">Donate <span>Brightwell Global</span></div>
<div class="abs donate-text">Lorem Ipsum has been the industry's standard dummy text ever</div>
<div class="abs btn" style="left:498px;top:937px;width:57px;height:20px;font-size:9px">DONATE</div>

<!-- footer -->
<div class="abs footer"></div>
<div class="abs f-col" style="left:60px;width:172px">
  <h4>LATEST NEWS</h4>
  <div>27/JULY/2015</div>
  <div>Donec consectetur diam ac nibh auctor ultricies. Integer mauris lacus, consequat in luctus id, semper sed felis. Cum sociis natoque penatibus</div>
  <div style="text-align:right;font-size:6.5px;margin-top:2px">READ MORE &nbsp;&raquo;</div>
</div>
<div class="abs f-divider" style="left:266px"></div>
<div class="abs f-col" style="left:302px">
  <h4>GET IN TOUCH</h4>
  <div style="margin-top:10px">1840 Harbor View Rd. Suite 210</div>
  <div>Maple Grove, ON K2P 1L4</div>
  <div>Phone 613-555-0187</div>
  <div>Email: hello@brightwellglobal.org</div>
</div>
<div class="abs f-divider" style="left:468px"></div>
<div class="abs f-col" style="left:518px;width:190px">
  <h4>SUBSCRIBE TO NEWS</h4>
  <div style="padding-left:2px;line-height:12px">enter your email to receive Brightwell news<br>&amp; updates!</div>
</div>
<div class="abs email">Enter Your Email Address</div>
<div class="abs submit">SUBMIT</div>

<div class="abs bottom"></div>
<div class="abs legal">Privacy Policy &nbsp;| &nbsp;Terms Conditions &nbsp;| &nbsp;Sitemap &nbsp;| &nbsp;Contact Us</div>
<div class="abs copy">Copyright © 2015 &nbsp;All Rights Reserved</div>
<div class="abs social">
  <i style="background:#f2a31b"></i><i style="background:#2fa4de"></i><i style="background:#3b5b9a"></i><i style="background:#2f7bd0"></i><i style="background:#38a3d4"></i><i style="background:#d8202a"></i>
</div>

</body>
</html>
```